QP Fiduciary Website Redesign Contest

We want to refresh our website to be more insitutional, professional for an international audience. We have designed a new logo for this purpose and that has been attached. A full brand brief and positioning statement has also been attached. Please read through all the documents carefully before designing. The old website is found here: https://qp-fiduciary.example/

Target Market(s)

Actuaries and associated businesses internationally

Industry/Entity Type

professional services - actuaries

Number of Pages Required

3 page

Font styles to use
Sans Serif

Colors
0054AA
0677BA
7BADD7
CADEEF
E8F1F8
0094D4
00A9DD
6FCCEA
C7EBF8
E9F6FB
F0912C
F2A743
F7CA91
FBE8D2
FDF5EE
EE7325
F08F49
F5BC92
FAE3D3
FDF4ED
EB3D1F
EC4F4E
F09395
F8D3D4
FCEDEE

Requirements
Must have
• blues and greens to match the logo color, complimentary colors, navigation
Nice to have
• old site: https://qp-fiduciary.example/

```html
<!DOCTYPE html>
<html lang="en">
<head>
<meta charset="utf-8">
<title>QP Fiduciary — Actuarial Software</title>
<link href="https://fonts.googleapis.com/css2?family=Poppins:wght@400;500;600;700;800&display=swap" rel="stylesheet">
<style>
:root{
  --navy:#0a3a9c;
  --blue:#0054AA;
  --bright-blue:#1d4fe0;
  --line-blue:#2a7be0;
  --ring:#3aa6e6;
  --disc:#e5f2fb;
  --pale-2:#f1f6fb;
  --orange:#ff6a0c;
  --ink:#3a3a3a;
  --text:#2b2b2b;
  --white:#ffffff;
  --footer:#262626;
}
*{box-sizing:border-box;margin:0;padding:0}
html,body{width:1200px;height:3573px;overflow:hidden}
body{position:relative;font-family:"Poppins",sans-serif;color:var(--text);background:var(--white)}
.abs{position:absolute}
.btn{position:absolute;display:flex;align-items:center;justify-content:center;background:var(--orange);color:var(--white);font-weight:700;font-size:12px;letter-spacing:.3px;text-transform:uppercase;text-decoration:none}
.section-title{position:absolute;left:0;width:1200px;text-align:center;font-weight:700;font-size:36px;letter-spacing:.5px;color:var(--ink);text-transform:uppercase}

/* header */
.site-header{position:absolute;left:0;top:0;width:1200px;height:82px;background:var(--white)}
.brand{position:absolute;font-weight:600;font-size:28px;letter-spacing:1.5px;color:var(--navy);text-transform:uppercase}
.nav a{position:absolute;top:38px;font-size:12px;font-weight:600;color:#333;text-decoration:none;text-transform:uppercase}
.nav a.active{color:var(--bright-blue)}

/* hero */
.hero{position:absolute;left:0;top:82px;width:1200px;height:570px;background:linear-gradient(120deg,#1640c9 0%,#1c55ea 55%,#1b4fd8 100%);overflow:hidden}
.hero h1{position:absolute;left:74px;top:145px;width:640px;font-size:38px;line-height:42px;font-weight:700;color:var(--white);text-transform:uppercase;letter-spacing:.5px}
.hero p{position:absolute;left:74px;top:277px;width:600px;font-size:18.5px;line-height:28px;color:var(--white)}
.hero-art{position:absolute;left:610px;top:70px;width:580px;height:460px;
  background:
    radial-gradient(ellipse 38% 30% at 45% 62%,rgba(255,106,12,.55),rgba(255,106,12,0) 70%),
    radial-gradient(ellipse 30% 26% at 62% 40%,rgba(10,14,30,.45),rgba(10,14,30,0) 70%),
    radial-gradient(ellipse 48% 44% at 52% 52%,rgba(225,232,248,.35),rgba(225,232,248,0) 72%)}

/* overview */
.step{position:absolute;background:var(--white);box-shadow:0 4px 16px rgba(0,0,0,.12);border-radius:3px;display:flex;flex-direction:column;align-items:center;justify-content:center;gap:16px;font-size:23px;color:#333}
.accent{position:absolute}
.overview-text{position:absolute;left:100px;top:1080px;width:1000px;text-align:center;font-size:17px;line-height:31px;color:#333}

/* solutions */
.solutions{position:absolute;left:0;top:1290px;width:1200px;height:507px;background:var(--pale-2)}
.solution{position:absolute;top:156px;height:278px;background:var(--white);text-align:center;padding-top:40px}
.solution h3{font-size:23px;line-height:29px;font-weight:700;color:var(--blue);margin-top:10px}
.solution p{font-size:15px;line-height:24px;color:#333;margin:6px auto 0;width:280px}

/* characteristics */
.trait{position:absolute;top:1956px;width:250px;height:250px}
.trait-disc{position:absolute;left:31px;top:31px;width:188px;height:188px;border-radius:50%;background:var(--disc);display:flex;align-items:center;justify-content:center}
.trait-caption{position:absolute;width:190px;text-align:center;font-size:16px;line-height:22px;color:#333}

/* insights */
.insights{position:absolute;left:0;top:2367px;width:1200px;height:593px;background:var(--pale-2)}
.insight-img{position:absolute;top:136px;width:329px;height:215px}
.insight-title{position:absolute;top:368px;width:330px;font-size:21px;line-height:29px;font-weight:600;color:var(--blue)}
.read-more{position:absolute;top:434px;font-size:15px;font-weight:600;color:#222;text-decoration:underline}

/* footer */
.site-footer{position:absolute;left:0;top:3278px;width:1200px;height:295px;background:var(--footer);color:var(--white)}
.site-footer h4{position:absolute;top:55px;font-size:16px;font-weight:600;text-transform:uppercase}
.site-footer .line{position:absolute;font-size:15px;color:#e6e6e6}
</style>
</head>
<body>

<header class="site-header">
  <div class="brand" style="left:74px;top:24px">QP Fiduciary</div>
  <nav class="nav">
    <a class="active" style="left:349px">Home</a>
    <a style="left:412px">Platform</a>
    <a style="left:503px">Solutions</a>
    <a style="left:599px">Insights</a>
    <a style="left:683px">Company</a>
    <a style="left:774px">Contact</a>
  </nav>
  <a class="btn" style="left:857px;top:24px;width:270px;height:39px">Request Technical Walkthrough</a>
</header>

<section class="hero">
  <div class="hero-art" role="img" aria-label="Abstract geometric composition of blue, orange, black and pale shapes"></div>
  <h1>Actuarial software<br>for structured, auditable<br>financial analysis</h1>
  <p>Software that translates actuarial methodologies into<br>disciplined decision-ready analytical tools across diverse<br>regulatory environments.</p>
  <a class="btn" style="left:74px;top:379px;width:270px;height:39px">Request Technical Walkthrough</a>
</section>

<h2 class="section-title" style="top:726px">Platform Overview</h2>

<div class="accent" style="left:74px;top:810px;width:152px;height:209px;background:linear-gradient(180deg,#7fd0ea,#5ab2e0);border-radius:4px"></div>
<div class="accent" style="left:395px;top:810px;width:151px;height:20px;background:var(--blue);border-radius:4px 4px 0 0"></div>
<div class="accent" style="left:670px;top:999px;width:150px;height:20px;background:var(--blue);border-radius:0 0 4px 4px"></div>
<div class="accent" style="left:988px;top:810px;width:152px;height:209px;background:var(--orange);border-radius:4px"></div>

<div class="step" style="left:88px;top:825px;width:229px;height:179px">
  <svg width="48" height="48" viewBox="0 0 24 24" fill="none" stroke="#333" stroke-width="2.6" stroke-linecap="round"><path d="M20 11a8 8 0 0 0-14.5-4.5M4 13a8 8 0 0 0 14.5 4.5"/><path d="M5 3v4h4M19 21v-4h-4"/></svg>
  <span>Input</span>
</div>
<div class="step" style="left:356px;top:825px;width:228px;height:179px">
  <svg width="46" height="40" viewBox="0 0 24 20" fill="#333"><rect x="1" y="0" width="2" height="19"/><rect x="1" y="17" width="22" height="2"/><rect x="6" y="8" width="2.5" height="8"/><rect x="10.5" y="4" width="2.5" height="12"/><rect x="15" y="9" width="2.5" height="7"/><rect x="19.5" y="6" width="2.5" height="10"/></svg>
  <span>Analysis</span>
</div>
<div class="step" style="left:631px;top:825px;width:229px;height:179px">
  <svg width="46" height="40" viewBox="0 0 24 20" fill="#333"><rect x="0" y="0" width="4" height="4"/><rect x="6" y="0" width="18" height="4"/><rect x="0" y="8" width="4" height="4"/><rect x="6" y="8" width="18" height="4"/><rect x="0" y="16" width="4" height="4"/><rect x="6" y="16" width="18" height="4"/></svg>
  <span>Review</span>
</div>
<div class="step" style="left:898px;top:825px;width:228px;height:179px">
  <svg width="34" height="48" viewBox="0 0 16 24" fill="#333"><path d="M8 0a8 8 0 0 0-5 14c1 1 1.5 2 1.5 3h7c0-1 .5-2 1.5-3A8 8 0 0 0 8 0z"/><rect x="4.5" y="18.5" width="7" height="2" rx="1"/><rect x="5.5" y="21.5" width="5" height="2" rx="1"/></svg>
  <span>Output</span>
</div>

<svg class="abs" style="left:295px;top:968px" width="50" height="12" viewBox="0 0 50 12"><path d="M0 6h42" stroke="var(--bright-blue)" stroke-width="2"/><path d="M40 1l9 5-9 5z" fill="var(--bright-blue)"/></svg>
<svg class="abs" style="left:563px;top:843px" width="50" height="12" viewBox="0 0 50 12"><path d="M0 6h42" stroke="var(--bright-blue)" stroke-width="2"/><path d="M40 1l9 5-9 5z" fill="var(--bright-blue)"/></svg>
<svg class="abs" style="left:839px;top:968px" width="50" height="12" viewBox="0 0 50 12"><path d="M0 6h42" stroke="var(--bright-blue)" stroke-width="2"/><path d="M40 1l9 5-9 5z" fill="var(--bright-blue)"/></svg>

<p class="overview-text">QP Fiduciary develops modular actuarial software designed to support reserving, valuation, pricing, and risk analysis workflows across diverse regulatory environments.</p>
<a class="btn" style="left:503px;top:1171px;width:193px;height:39px">Explore Platform</a>

<section class="solutions">
  <h2 class="section-title" style="top:64px">Core Solutions</h2>
  <div class="accent" style="left:62px;top:144px;width:96px;height:96px;background:var(--blue)"></div>
  <div class="accent" style="left:1042px;top:350px;width:97px;height:96px;background:var(--orange)"></div>
  <div class="solution" style="left:74px;width:329px">
    <svg width="34" height="40" viewBox="0 0 20 24" fill="none" stroke="#333" stroke-width="2"><path d="M2 1h11l5 5v17H2z"/><path d="M6 11h8M6 15h8M6 19h5"/></svg>
    <h3>Reserving &amp; Valuation</h3>
    <p>Software supporting structured reserving workflows and financial reporting across jurisdictions.</p>
  </div>
  <div class="solution" style="left:431px;width:339px;top:151px;height:288px;border:4px solid #bdd0ea;border-radius:4px">
    <svg width="28" height="42" viewBox="0 0 16 24" fill="none" stroke="#333" stroke-width="2.4"><path d="M8 0v24M13 6c-1-2-3-2.5-5-2.5S3 4.5 3 7s3 3 5 3.8 5 1.5 5 4.2-2.5 3.5-5 3.5-4.5-.8-5.5-2.5"/></svg>
    <h3>Pricing</h3>
    <p>Models supporting insurance and reinsurance pricing based on actuarial methodologies.</p>
  </div>
  <div class="solution" style="left:797px;width:329px">
    <svg width="42" height="36" viewBox="0 0 24 20" fill="#333"><rect x="0" y="2" width="24" height="2"/><rect x="0" y="9" width="24" height="2"/><rect x="0" y="16" width="24" height="2"/><rect x="5" y="0" width="3" height="6"/><rect x="15" y="7" width="3" height="6"/><rect x="8" y="14" width="3" height="6"/></svg>
    <h3>Enterprise<br>Risk Management</h3>
    <p>Software supporting reinsurance optimization and capital modeling.</p>
  </div>
</section>

<h2 class="section-title" style="top:1875px">Platform Characteristics</h2>

<div class="trait" style="left:83px">
  <svg width="250" height="250" viewBox="0 0 250 250"><path d="M125 5A120 120 0 0 0 5 125" fill="none" stroke="var(--ring)" stroke-width="2"/><path d="M5 125A120 120 0 0 0 245 140" fill="none" stroke="var(--ring)" stroke-width="2"/><path d="M145 7A120 120 0 0 1 245 120" fill="none" stroke="var(--line-blue)" stroke-width="5" stroke-dasharray="1 12" stroke-linecap="round"/><circle cx="5" cy="125" r="5" fill="#fff" stroke="var(--ring)" stroke-width="2"/></svg>
  <div class="trait-disc">
    <svg width="96" height="96" viewBox="0 0 96 96" fill="none" stroke-width="2.5" stroke-linecap="round" stroke-linejoin="round">
      <rect x="10" y="12" width="24" height="16" stroke="var(--orange)"/><path d="M15 18h14M15 23h10" stroke="var(--orange)"/>
      <circle cx="48" cy="50" r="13" stroke="var(--line-blue)"/><circle cx="48" cy="50" r="20" stroke="var(--line-blue)" stroke-dasharray="5 5"/>
      <path d="M42 50l4 4 8-8" stroke="var(--orange)"/>
      <path d="M40 18h20a10 10 0 0 1 10 10" stroke="var(--line-blue)"/><path d="M66 24l4 5 4-5" stroke="var(--line-blue)"/>
      <path d="M26 58a18 18 0 0 0 10 18h10" stroke="var(--line-blue)"/>
      <rect x="60" y="68" width="24" height="16" stroke="var(--line-blue)"/><path d="M65 74h14M65 79h10" stroke="var(--line-blue)"/>
    </svg>
  </div>
</div>
<div class="trait" style="left:337px">
  <svg width="250" height="250" viewBox="0 0 250 250"><path d="M5 125A120 120 0 0 1 245 110" fill="none" stroke="var(--ring)" stroke-width="2"/><path d="M5 125A120 120 0 0 0 105 243" fill="none" stroke="var(--ring)" stroke-width="2"/><path d="M125 245A120 120 0 0 0 245 130" fill="none" stroke="var(--line-blue)" stroke-width="5" stroke-dasharray="1 12" stroke-linecap="round"/><circle cx="245" cy="125" r="5" fill="#fff" stroke="var(--ring)" stroke-width="2"/></svg>
  <div class="trait-disc">
    <svg width="96" height="96" viewBox="0 0 96 96" fill="none" stroke-width="2.5" stroke-linecap="round" stroke-linejoin="round">
      <path d="M22 10h36l10 10v56H22z" stroke="var(--line-blue)"/>
      <path d="M30 22h20" stroke="var(--orange)"/><path d="M30 32h30M30 40h18M30 48h14M30 56h14M30 64h20" stroke="var(--line-blue)"/>
      <circle cx="62" cy="58" r="12" stroke="var(--line-blue)" fill="var(--disc)"/><path d="M56 58h12M62 52v12" stroke="var(--orange)"/>
      <path d="M71 67l12 12" stroke="var(--line-blue)" stroke-width="4"/>
    </svg>
  </div>
</div>
<div class="trait" style="left:611px">
  <svg width="250" height="250" viewBox="0 0 250 250"><path d="M125 5A120 120 0 0 0 5 125A120 120 0 0 0 245 125" fill="none" stroke="var(--ring)" stroke-width="2"/><path d="M145 7A120 120 0 0 1 245 110" fill="none" stroke="var(--line-blue)" stroke-width="5" stroke-dasharray="1 12" stroke-linecap="round"/></svg>
  <div class="trait-disc">
    <svg width="96" height="96" viewBox="0 0 96 96" fill="none" stroke-width="2.5" stroke-linecap="round" stroke-linejoin="round">
      <rect x="12" y="14" width="52" height="64" stroke="var(--line-blue)"/><rect x="18" y="20" width="52" height="64" stroke="var(--line-blue)" fill="var(--disc)"/>
      <path d="M26 40l10-8 10 6 12-10" stroke="var(--orange)"/>
      <path d="M26 76V64M34 76V58M42 76V66M50 76V60" stroke="var(--line-blue)"/>
      <path d="M26 50h16M26 55h12" stroke="var(--line-blue)"/>
      <circle cx="66" cy="44" r="12" stroke="var(--line-blue)" fill="var(--disc)"/>
      <path d="M75 53l10 12" stroke="var(--line-blue)" stroke-width="4"/>
    </svg>
  </div>
</div>
<div class="trait" style="left:867px">
  <svg width="250" height="250" viewBox="0 0 250 250"><path d="M5 125A120 120 0 0 1 245 110" fill="none" stroke="var(--ring)" stroke-width="2"/><path d="M5 125A120 120 0 0 0 105 243" fill="none" stroke="var(--ring)" stroke-width="2"/><path d="M125 245A120 120 0 0 0 245 130" fill="none" stroke="var(--line-blue)" stroke-width="5" stroke-dasharray="1 12" stroke-linecap="round"/><circle cx="245" cy="115" r="5" fill="#fff" stroke="var(--ring)" stroke-width="2"/></svg>
  <div class="trait-disc">
    <svg width="96" height="96" viewBox="0 0 96 96" fill="none" stroke-width="2.5" stroke-linecap="round" stroke-linejoin="round">
      <rect x="18" y="16" width="44" height="62" rx="3" stroke="var(--line-blue)"/>
      <rect x="30" y="11" width="20" height="10" rx="2" stroke="var(--orange)" fill="var(--disc)"/>
      <path d="M27 34h26M27 44h26M27 54h16" stroke="var(--line-blue)"/>
      <circle cx="64" cy="64" r="15" stroke="var(--line-blue)" fill="var(--disc)"/>
      <path d="M57 64l5 5 9-9" stroke="var(--orange)"/>
    </svg>
  </div>
</div>

<p class="trait-caption" style="left:113px;top:2224px">Structured workflows suitable for multi-jurisdictional review</p>
<p class="trait-caption" style="left:367px;top:2224px">Transparent assumptions and methodological clarity</p>
<p class="trait-caption" style="left:641px;top:2224px">Comparative scenario analysis</p>
<p class="trait-caption" style="left:897px;top:2224px">Supports professional judgment rather than replacing it</p>

<section class="insights">
  <h2 class="section-title" style="top:58px">Insights</h2>
  <div class="insight-img" style="left:74px;background:linear-gradient(135deg,#f05aa8,#f4d23c 40%,#3cc6d8 75%,#8e5ae0)" role="img" aria-label="Colourful field of isometric cubes"></div>
  <div class="insight-img" style="left:435px;background:linear-gradient(135deg,#f6927f,#9fd0dc 55%,#f28a78)" role="img" aria-label="Pastel coral and teal architectural shapes with a laptop"></div>
  <div class="insight-img" style="left:797px;background:linear-gradient(160deg,#0a1640,#1b3d8f 55%,#20a7c9)" role="img" aria-label="Glowing digital grid of circuit blocks"></div>
  <h3 class="insight-title" style="left:74px">Methodological perspectives in actuarial reserving.</h3>
  <h3 class="insight-title" style="left:435px">Governance considerations in multi-jurisdictional analysis</h3>
  <h3 class="insight-title" style="left:797px">Observations on actuarial practice in emerging markets</h3>
  <a class="read-more" style="left:74px">Read More</a>
  <a class="read-more" style="left:435px">Read More</a>
  <a class="read-more" style="left:797px">Read More</a>
  <a class="btn" style="left:503px;top:497px;width:193px;height:39px">Read Insights</a>
</section>

<h2 class="section-title" style="top:3036px;line-height:44px">Interested in exploring<br>the platform?</h2>
<a class="btn" style="left:465px;top:3161px;width:270px;height:39px">Request Technical Walkthrough</a>

<footer class="site-footer">
  <div class="brand" style="left:74px;top:50px;color:var(--white)">QP Fiduciary</div>
  <p class="line" style="left:74px;top:118px;line-height:25px">Copyright© 2026 Company Name<br>All Rights Reserved.</p>
  <a class="line" style="left:74px;top:177px;color:var(--orange);text-decoration:underline">Legal</a>

  <h4 style="left:404px">Quick Links</h4>
  <p class="line" style="left:404px;top:93px">Company</p>
  <p class="line" style="left:404px;top:127px">Platform</p>
  <p class="line" style="left:404px;top:160px">Solutions</p>
  <p class="line" style="left:404px;top:194px">Insights</p>
  <p class="line" style="left:404px;top:227px">Contact</p>

  <h4 style="left:615px">Contact Info</h4>
  <p class="line" style="left:615px;top:93px;line-height:26px">410 Harbor Crest Ave, Suite<br>200 Lakeview, FL 33000</p>
  <p class="line" style="left:615px;top:155px">+1(555)010-2468</p>
  <p class="line" style="left:615px;top:184px">contact@qp-fiduciary.example</p>

  <h4 style="left:908px">Get Connect Us</h4>
  <div class="abs" style="left:908px;top:95px;width:20px;height:20px;background:var(--orange);border-radius:2px"></div>
</footer>

</body>
</html>
```